Redesign Fitness Photos for Facebook Ads Needed

We are a fun, energetic, group fitness facility that needs to have a few (3) photos doctored up and turned into ads for Facebook & Instagram.
I would like the photos to be doctored up so that they are clear, bright, energetic.  Feel free to manipulate the photos, backgrounds, cropping, cutting as needed.
I would like to include text on photos:
Pulsora
New Year
Challenge
* Fitness Training  * Nutritional Support * Motivation & Support
Join Now
The text should be roughly the size of the examples included in order to comply with facebooks text size requirements
I have included 3 examples of another gyms ads which I like how the images are eye catching and text is clearly visible and pops with color.
Although I have attached multiple images that can be used,  I am only looking for 3 completed designs to be used for ads.

You choose the images that you feel you can modify the best.
I look forward to seeing your design.
Thank you.

```html
<!DOCTYPE html>
<html lang="en">
<head>
<meta charset="utf-8">
<title>Pulsora – New Year Challenge</title>
<link rel="stylesheet" href="https://fonts.googleapis.com/css2?family=Oswald:wght@500;600;700&family=Poppins:ital,wght@0,500;0,600;1,800&display=swap">
<style>
  :root {
    --bg-dark: #1e1f22;
    --brand-blue: #0097f5;
    --white: #ffffff;
    --muted: #c9ccd1;
    --pill-edge: #2a2b2f;
    --photo-purple: #5b3fb0;
    --photo-pink: #c8357a;
    --photo-blue: #3b63c9;
  }
  html, body {
    margin: 0;
    padding: 0;
    width: 1200px;
    height: 1200px;
    overflow: hidden;
    background: #f7f7f7;
  }
  .ad {
    position: relative;
    width: 1200px;
    height: 1200px;
    overflow: hidden;
    background: var(--bg-dark);
    font-family: "Oswald", "Arial Narrow", sans-serif;
  }
  .ad-backdrop {
    position: absolute;
    inset: 0;
    background:
      radial-gradient(ellipse at 55% 65%, rgba(90,92,98,.55), transparent 60%),
      radial-gradient(ellipse at 20% 70%, rgba(70,72,78,.5), transparent 55%),
      linear-gradient(160deg, #2b2c30 0%, #232427 45%, #1b1c1f 100%);
  }
  .dot-grid {
    position: absolute;
    background: linear-gradient(135deg, rgba(120,124,132,.18), rgba(120,124,132,.08));
    border-radius: 2px;
  }
  .dot-grid--top { left: 1032px; top: 70px; width: 105px; height: 105px; }
  .dot-grid--bottom { left: 832px; top: 1040px; width: 330px; height: 101px; }

  .brand {
    position: absolute;
    left: 0; right: 0;
    top: 72px;
    text-align: center;
    color: var(--white);
  }
  .brand-name {
    display: inline-flex;
    align-items: center;
    gap: 10px;
    font-family: "Poppins", sans-serif;
    font-weight: 600;
    font-size: 50px;
    line-height: 1;
    letter-spacing: .5px;
  }
  .brand-mark {
    width: 18px; height: 18px;
    background: var(--brand-blue);
  }
  .brand-tagline {
    margin-top: 6px;
    font-family: "Poppins", sans-serif;
    font-weight: 500;
    font-size: 11px;
    letter-spacing: 3px;
    color: var(--muted);
  }

  .headline-kicker {
    position: absolute;
    left: 0; right: 0;
    top: 178px;
    margin: 0;
    text-align: center;
    color: var(--white);
    font-weight: 700;
    font-style: italic;
    font-size: 60px;
    line-height: 1;
    letter-spacing: 1px;
  }
  .kicker-burst {
    position: absolute;
    top: 180px;
  }
  .kicker-burst--left { left: 358px; }
  .kicker-burst--right { left: 742px; }

  .headline-main {
    position: absolute;
    left: 0; right: 0;
    top: 240px;
    margin: 0;
    text-align: center;
    color: var(--brand-blue);
    font-weight: 700;
    font-style: italic;
    font-size: 178px;
    line-height: 1;
    letter-spacing: 2px;
  }

  .photo {
    position: absolute;
    box-shadow: 0 6px 16px rgba(0,0,0,.5);
  }
  .photo--ropes { left: 446px; top: 518px; width: 204px; height: 204px;
    background: linear-gradient(150deg, #7d6cc4 0%, #5c5870 50%, #3a3a40 100%); }
  .photo--team { left: 827px; top: 449px; width: 273px; height: 273px;
    background: linear-gradient(170deg, var(--photo-pink) 0%, var(--photo-purple) 35%, #2e2a44 100%); }
  .photo--duo { left: 522px; top: 740px; width: 204px; height: 203px;
    background: linear-gradient(170deg, var(--photo-purple) 0%, var(--photo-blue) 55%, #2b2c40 100%); }
  .photo--group { left: 743px; top: 740px; width: 263px; height: 257px;
    background: linear-gradient(170deg, #c84060 0%, #6a4c9c 35%, #3a3a4a 100%); }

  .accent-square {
    position: absolute;
    background: var(--brand-blue);
  }
  .accent-square--a { left: 668px; top: 582px; width: 140px; height: 140px; }
  .accent-square--b { left: 1100px; top: 410px; width: 36px; height: 37px; }
  .accent-square--c { left: 1022px; top: 740px; width: 140px; height: 139px; }
  .accent-square--d { left: 629px; top: 961px; width: 95px; height: 93px; }

  .benefits {
    position: absolute;
    left: 75px;
    top: 810px;
    margin: 0;
    padding: 0;
    list-style: none;
    color: var(--white);
    font-weight: 600;
    font-style: italic;
    font-size: 40px;
    line-height: 50px;
    letter-spacing: .3px;
  }

  .cta {
    position: absolute;
    left: 75px;
    top: 1062px;
    display: flex;
    align-items: center;
  }
  .cta-button {
    width: 340px;
    height: 76px;
    border-radius: 40px;
    background: var(--white);
    border: 4px solid var(--pill-edge);
    display: flex;
    align-items: center;
    justify-content: center;
    color: var(--brand-blue);
    font-family: "Poppins", sans-serif;
    font-weight: 800;
    font-style: italic;
    font-size: 46px;
    letter-spacing: -1px;
    text-decoration: none;
  }
</style>
</head>
<body>
  <main class="ad">
    <div class="ad-backdrop" role="img" aria-label="Dimmed gym scene of a woman squatting with a loaded barbell"></div>
    <div class="dot-grid dot-grid--top" role="img" aria-label="Dot grid accent"></div>
    <div class="dot-grid dot-grid--bottom" role="img" aria-label="Dot grid accent"></div>

    <header class="brand">
      <div class="brand-name"><span class="brand-mark"></span>Pulsora</div>
      <div class="brand-tagline">Personal Group Training</div>
    </header>

    <svg class="kicker-burst kicker-burst--left" width="92" height="46" viewBox="0 0 92 46" aria-hidden="true">
      <g stroke="#fff" stroke-width="2" stroke-linecap="round">
        <line x1="2" y1="2" x2="58" y2="18"/>
        <line x1="60" y1="6" x2="86" y2="22"/>
        <line x1="58" y1="38" x2="86" y2="35"/>
      </g>
    </svg>
    <div class="headline-kicker">NEW YEAR</div>
    <svg class="kicker-burst kicker-burst--right" width="92" height="46" viewBox="0 0 92 46" aria-hidden="true">
      <g stroke="#fff" stroke-width="2" stroke-linecap="round">
        <line x1="90" y1="8" x2="34" y2="20"/>
        <line x1="22" y1="4" x2="4" y2="22"/>
        <line x1="6" y1="38" x2="34" y2="38"/>
      </g>
    </svg>
    <h1 class="headline-main">CHALLENGE</h1>

    <div class="accent-square accent-square--b"></div>
    <div class="photo photo--ropes" role="img" aria-label="Member training with battle ropes in the studio"></div>
    <div class="accent-square accent-square--a"></div>
    <div class="photo photo--team" role="img" aria-label="Five members flexing in front of a neon wall"></div>
    <div class="photo photo--duo" role="img" aria-label="Two members in blue tank tops flexing"></div>
    <div class="photo photo--group" role="img" aria-label="Large class group photo on the gym floor"></div>
    <div class="accent-square accent-square--c"></div>
    <div class="accent-square accent-square--d"></div>

    <ul class="benefits">
      <li>FITNESS TRAINING</li>
      <li>MOTIVATION &amp; SUPPORT</li>
      <li>NUTRITIONAL SUPPORT</li>
    </ul>

    <div class="cta">
      <svg width="50" height="30" viewBox="0 0 50 30" aria-hidden="true">
        <g fill="#fff">
          <rect x="0" y="9" width="4" height="12"/>
          <rect x="7" y="4" width="5" height="22"/>
          <rect x="14" y="2" width="5" height="26"/>
          <rect x="19" y="13.5" width="31" height="3"/>
        </g>
      </svg>
      <a class="cta-button" href="#">JOIN NOW</a>
      <svg width="50" height="30" viewBox="0 0 50 30" aria-hidden="true">
        <g fill="#fff">
          <rect x="0" y="13.5" width="31" height="3"/>
          <rect x="31" y="2" width="5" height="26"/>
          <rect x="38" y="4" width="5" height="22"/>
          <rect x="46" y="9" width="4" height="12"/>
        </g>
      </svg>
    </div>
  </main>
</body>
</html>
```